BLS Business Card 2018

Larkmere Chiropractic. We have two locations that we want to advertise on the same card. Brightvale OrthoCore campus address: 3815 Pellham Dr., Suite 240, Flowood, MS 39417. Madison address: 246 Willowmere Dr., Building D., Madison, MS 39284. website: www.drlarkmere-example.com. o:(601)555-0147 f:(601)555-0183

Target Market(s)

Health care decision makers: primary care doctors and mothers

Contact Information for Business Card

I have no idea; up for any suggestions and I'd do much better picking from examples versus describing what I'm looking for. We are in a very high end location and would like the cards to look really sharp.

Requirements
Must have
• My name, Martin R Belvane, D.C.

```html
<!DOCTYPE html>
<html lang="en">
<head>
<meta charset="utf-8">
<title>Larkmere Chiropractic – Business Card</title>
<link href="https://fonts.googleapis.com/css2?family=Open+Sans:wght@400;600;700&family=Open+Sans+Condensed:wght@700&display=swap" rel="stylesheet">
<style>
  :root {
    --canvas: #e9e8e6;
    --paper: #f7f7f7;
    --ink: #111111;
    --ink-soft: #6b6b6b;
    --logo-grey: #8a8a8a;
    --band: #0b0b0b;
    --band-edge: #8f8f8f;
    --reverse: #050505;
    --figure-tone: #2a2a2a;
    --white: #ffffff;
  }
  * { margin: 0; padding: 0; box-sizing: border-box; }
  html, body {
    width: 1200px; height: 950px; overflow: hidden;
    background: var(--canvas);
    font-family: "Open Sans", Arial, sans-serif;
  }
  .canvas {
    position: relative; width: 1200px; height: 950px;
  }
  .card {
    position: absolute; left: 250px;
    width: 700px; height: 400px;
    box-shadow: 0 8px 24px rgba(0,0,0,.18);
    overflow: hidden;
  }
  .card-front { top: 55px; background: var(--paper); }
  .card-back { top: 495px; background: var(--reverse); }

  .front-band { position: absolute; inset: 0; width: 700px; height: 400px; }

  .brand {
    position: absolute; left: 48px; top: 128px;
    display: flex; align-items: center; gap: 14px;
  }
  .brand-mark {
    width: 34px; height: 34px; background: var(--logo-grey);
  }
  .brand-name {
    font-family: "Open Sans", Arial, sans-serif;
    font-weight: 400; color: var(--logo-grey);
    font-size: 25px; line-height: 1.1; letter-spacing: .04em;
    text-transform: uppercase;
  }
  .brand-name span { display: block; font-size: 17px; letter-spacing: .2em; }

  .details {
    position: absolute; left: 360px; top: 42px;
  }
  .doctor-name {
    font-family: "Open Sans Condensed", "Open Sans", Arial, sans-serif;
    font-weight: 700; font-size: 22px; color: var(--ink);
    letter-spacing: .01em; margin-bottom: 12px;
  }
  .location { font-size: 14px; line-height: 1.5; color: var(--ink-soft); }
  .location + .location { margin-top: 6px; }

  .contact-line {
    position: absolute; left: 40px; bottom: 28px;
    font-size: 14px; color: var(--white); letter-spacing: .01em;
    white-space: nowrap;
  }
  .contact-line b { font-weight: 700; }

  .figure-area {
    position: absolute; left: 210px; top: 110px;
    width: 280px; height: 180px;
    border-radius: 50%;
    background: radial-gradient(ellipse at center, var(--figure-tone) 0%, var(--reverse) 70%);
  }
</style>
</head>
<body>
<main class="canvas">

  <section class="card card-front" aria-label="Business card front">
    <svg class="front-band" viewBox="0 0 700 400" aria-hidden="true">
      <path d="M0 372 C 180 372, 300 360, 420 318 C 540 276, 620 250, 700 246 L700 400 L0 400 Z" fill="var(--band-edge)"/>
      <path d="M0 380 C 180 380, 300 368, 420 326 C 540 284, 620 258, 700 254 L700 400 L0 400 Z" fill="var(--band)" transform="translate(0,-40) scale(1,1.1)"/>
      <path d="M0 330 C 180 330, 300 318, 420 276 C 540 234, 620 208, 700 204 L700 400 L0 400 Z" fill="var(--band)"/>
    </svg>

    <div class="brand">
      <div class="brand-mark"></div>
      <div class="brand-name">Larkmere<span>Chiropractic</span></div>
    </div>

    <div class="details">
      <h1 class="doctor-name">MARTIN R BELVANE, D.C.</h1>
      <p class="location">Madison address:<br>246 Willowmere Dr., Building D.<br>Madison, MS 39284.</p>
      <p class="location">Brightvale OrthoCore campus :<br>3815 Pellham Dr., Suite 240<br>Flowood, MS 39417.</p>
    </div>

    <p class="contact-line"><b>Ph.</b> (601)555-0147 <b>Fax.</b> (601)555-0183 <b>Web.</b> www.drlarkmere-example.com</p>
  </section>

  <section class="card card-back" aria-label="Business card back">
    <div class="figure-area" role="img" aria-label="White line illustration of a reclining human back and shoulders"></div>
  </section>

</main>
</body>
</html>
```